Real Estate Business Card

Our Company, Brovan Real Estate needs a business card design. It will need a spot for our Name, Office Number, Cell number, email, website address. Brovanrealestate.example and Address. Please utilize our logo for the aesthetic feel of the card. We would like something that is noticeable but looks professional.

Please include our company tagline. "Where Finding Home Feels Simple and Clear"

Industry/Entity Type

Business

Requirements
Should not have
• Black colored Font is OK. But other than that no black

```html
<!DOCTYPE html>
<html lang="en">
<head>
<meta charset="utf-8">
<title>Brovan Real Estate – Business Card</title>
<link href="https://fonts.googleapis.com/css2?family=Source+Sans+3:ital,wght@0,400;0,600;0,700;1,700&display=swap" rel="stylesheet">
<style>
  :root {
    --stage: #3b3b3b;
    --paper: #e6e6e6;
    --brand-blue: #0b4c87;
    --brand-orange: #f47a20;
    --white: #ffffff;
  }
  * { box-sizing: border-box; margin: 0; padding: 0; }
  html, body { width: 1200px; height: 1000px; overflow: hidden; }
  body {
    position: relative;
    background: var(--stage);
    font-family: "Source Sans 3", Arial, sans-serif;
  }
  .card {
    position: absolute;
    background: var(--paper);
    overflow: hidden;
  }

  /* Front */
  .card-front { left: 42px; top: 40px; width: 745px; height: 447px; }
  .front-band {
    position: absolute; left: 0; top: 165px; width: 100%; height: 97px;
    background: var(--brand-blue);
    display: flex; align-items: center; justify-content: center; gap: 18px;
  }
  .front-band .brand-mark { width: 62px; height: 62px; background: var(--white); border-radius: 6px; }
  .front-band .brand-name { color: var(--white); font-size: 46px; font-weight: 600; letter-spacing: 0.5px; }
  .tagline {
    position: absolute; top: 265px; left: 286px;
    white-space: nowrap;
    color: var(--brand-orange); font-size: 16.5px; font-style: italic; font-weight: 700;
    letter-spacing: 0.2px;
  }

  /* Back */
  .card-back { left: 411px; top: 505px; width: 753px; height: 452px; }
  .back-brand {
    position: absolute; left: 62px; top: 88px;
    display: flex; align-items: center; gap: 18px;
  }
  .back-brand .brand-mark { width: 70px; height: 64px; background: var(--brand-blue); border-radius: 6px; }
  .back-brand .brand-name { color: var(--brand-blue); font-size: 46px; font-weight: 600; letter-spacing: 0.5px; }
  .contact-band {
    position: absolute; left: 0; top: 174px; width: 100%; height: 214px;
    background: var(--brand-blue);
  }
  .contact-list { list-style: none; position: absolute; left: 62px; top: 14px; }
  .contact-item {
    display: flex; align-items: center; height: 46px;
    color: var(--white); font-size: 18px; font-weight: 600;
  }
  .contact-item svg { width: 34px; height: 30px; margin-right: 13px; flex: none; }
  .icon-solid { fill: var(--white); }
  .icon-solid .cut { fill: var(--brand-blue); }
  .icon-line { fill: none; stroke: var(--white); stroke-width: 2; }
  .contact-item .light { font-weight: 400; }
  .person { position: absolute; right: 63px; top: 82px; text-align: right; }
  .person-name { color: var(--brand-orange); font-size: 29px; font-weight: 600; line-height: 1; }
  .person-title { color: var(--white); font-size: 21px; font-weight: 400; margin-top: 2px; }
  .accent-strip {
    position: absolute; left: 0; top: 395px; width: 100%; height: 57px;
    background: var(--brand-orange);
  }
</style>
</head>
<body>

<section class="card card-front">
  <div class="front-band">
    <span class="brand-mark"></span>
    <span class="brand-name">Brovan Real Estate</span>
  </div>
  <p class="tagline">Where Finding Home Feels Simple and Clear</p>
</section>

<section class="card card-back">
  <div class="back-brand">
    <span class="brand-mark"></span>
    <span class="brand-name">Brovan Real Estate</span>
  </div>

  <div class="contact-band">
    <ul class="contact-list">
      <li class="contact-item">
        <svg class="icon-solid" viewBox="0 0 34 30" aria-hidden="true"><path d="M2 9c0-4 7-6 15-6s15 2 15 6v3h-7V9H9v3H2z"/><path d="M8 13h18l3 14H5z"/><circle class="cut" cx="17" cy="20" r="4"/></svg>
        123 456 7890
      </li>
      <li class="contact-item">
        <svg class="icon-line" viewBox="0 0 34 30" aria-hidden="true"><circle cx="17" cy="15" r="13"/><ellipse cx="17" cy="15" rx="6" ry="13"/><path d="M4 15h26M6 8h22M6 22h22M17 2v26"/></svg>
        www.brovanrealestate.example
      </li>
      <li class="contact-item">
        <svg class="icon-line" viewBox="0 0 34 30" aria-hidden="true"><rect x="2" y="6" width="30" height="19"/><path d="M2 6l15 12L32 6M2 25l11-10M32 25L21 15"/></svg>
        yourname@brovanrealestate.example
      </li>
      <li class="contact-item">
        <svg class="icon-solid" viewBox="0 0 34 30" aria-hidden="true"><path d="M17 2L1 16h5v12h8v-8h6v8h8V16h5z"/></svg>
        Brovan Real Estate,&nbsp;<span class="light">City name, Country, NY 1234</span>
      </li>
    </ul>
    <div class="person">
      <p class="person-name">YOUR NAME</p>
      <p class="person-title">Title</p>
    </div>
  </div>
  <div class="accent-strip"></div>
</section>

</body>
</html>
```